Maple Beacon Website

We are starting a marketing company and to do that we need a website! We want a website that will inspire and persuade to bring out the awesomeness in our clients.
What we want to see:
- Inspirational and persuasive imagery that relate to Branding.
- No cliche images eg. business man, suits and hand shakes
- We want to transform and educate our clients.
- We want to show them the path and would like our website to really act as a guide that guides them step by step through our process.
- We want the portray that we are an investment but not have a pretentious way to it. We put our heart into every project and that is how we treat our clients.
-When you submit your design please include what platform you have created for. Preference would be Wordpress or Joobla.

We have included the psd file for the wire frame, logo files, font files, site map and a link to a video we create to give you more information on what we would like to see. http://clipvault.example/t/qk82LmZpr

Feel free to make small modification to the logos if you think it will improve it. Your creativity and advice is most welcome.
Updates

One thing we forgot. We would like to have our contact information near the top of the website as well as at the bottom.  Here is out contact info:

Email: info@maplebeacon.example
Phone: 587-555-0142

Project Deadline Extended
Reason: As we are new with the platform and that we want to optimize our results, we decided to extend the deadline by 15 days. Thanks!

Target Market(s)

28-60, Male and Female, Oil field, Local Businesses, Dentists, Chiropractors, Hair salon, Construction/Renovation, Events etc

Industry/Entity Type

Investment

Requirements
Must have
• - 4 Inspirational and persuasive Imagery for the top portion of the website
- Must have a feel as if your not on a website an example of this is linked below.
http://www.artbidhub.example/design/402957/web-design-by-lena-torvik
Nice to have
• - Creative advice from you.
- Creative buttons for Get Free Quote and Subscribe buttons. Something out of the box that draws peoples attention. eg. a 'B' button. Just and example but still something related to branding.
Should not have
• No Cliches

```html
<!DOCTYPE html>
<html lang="en">
<head>
<meta charset="utf-8">
<title>Maple Beacon</title>
<link rel="stylesheet" href="https://fonts.googleapis.com/css2?family=Source+Sans+3:ital,wght@0,400;0,600;0,700;1,600&family=Sansita:wght@700;800&display=swap">
<style>
:root{
  --page-top:#fbfbfb;
  --page-bottom:#e6e6e6;
  --rule-dark:#5a7a2a;
  --leaf:#6f9a2c;
  --green-text:#5f8a1e;
  --heading-green:#7a9a1e;
  --frame-green:#a8d42a;
  --band:#a3c750;
  --nav-text:#2f2f2f;
  --body-text:#575757;
  --tagline:#555;
  --button-top:#5a6270;
  --button-bottom:#353b45;
  --footer-top:#6f7d8d;
  --footer-bottom:#262c33;
  --white:#ffffff;
  --social-dark:#5d7b2e;
}
*{margin:0;padding:0;box-sizing:border-box}
html,body{width:1200px;height:792px;overflow:hidden}
body{
  position:relative;
  font-family:"Source Sans 3",Arial,sans-serif;
  background:linear-gradient(var(--page-top),var(--page-bottom) 330px,var(--page-top) 405px,var(--page-bottom) 690px);
  border-top:4px solid var(--rule-dark);
}
.brand{position:absolute;left:115px;top:22px;width:215px}
.brand-name{display:flex;align-items:center;gap:10px;font-weight:700;font-size:31px;color:#7f8387;letter-spacing:.5px;line-height:1}
.brand-dot{width:14px;height:14px;border-radius:50%;background:var(--leaf);flex:none}
.tagline{margin-top:30px;padding-left:30px;font-style:italic;font-weight:600;font-size:14px;color:var(--tagline)}
.main-nav{position:absolute;left:124px;top:128px;list-style:none}
.main-nav li{height:40px;display:flex;align-items:center;gap:10px;font-weight:600;font-size:14.5px;color:var(--nav-text);text-transform:uppercase}
.main-nav li.current{color:var(--green-text)}
.main-nav svg{width:17px;height:12px}
.hero{position:absolute;left:369px;top:6px;width:701px;height:316px;border:4px solid var(--frame-green)}
.hero-photo{position:absolute;inset:0;background:
  radial-gradient(ellipse at 30% 15%,#f4f9ec 0,#dcefc0 30%,transparent 60%),
  linear-gradient(180deg,#e9f3da 0%,#a9d25a 55%,#5e9a14 100%)}
.hero-title{position:absolute;right:34px;top:88px;font-family:"Sansita",Georgia,sans-serif;font-weight:800;font-size:38px;letter-spacing:1px;color:#4c6e1e}
.hero-dots{position:absolute;left:23px;bottom:8px;display:flex;gap:9px}
.hero-dots span{width:13px;height:13px;border-radius:50%;background:var(--white)}
.band{position:absolute;left:0;top:331px;width:1200px;height:70px;background:var(--band);border-top:1px solid #c7dd94}
.connect{position:absolute;left:107px;top:15px;font-family:"Sansita",sans-serif;font-weight:800;font-size:14px;line-height:14px;color:var(--white)}
.social{position:absolute;left:181px;top:18px;display:flex;gap:3px}
.social span{width:28px;height:28px;border-radius:50%;background:var(--white)}
.social span:first-child{background:var(--social-dark)}
.newsletter{position:absolute;left:362px;top:21px;font-family:"Sansita",sans-serif;font-weight:800;font-size:18.5px;letter-spacing:.3px;color:var(--white)}
.btn{position:absolute;top:18px;height:34px;display:flex;align-items:center;justify-content:center;font-weight:600;font-size:16px;color:var(--white);background:linear-gradient(var(--button-top),var(--button-bottom));border-radius:2px;letter-spacing:-.2px}
.btn-subscribe{left:828px;width:97px}
.btn-quote{left:932px;width:138px}
.welcome{position:absolute;left:279px;top:434px;width:641px}
.welcome h1{font-weight:700;font-size:22px;color:var(--heading-green);padding-bottom:3px;border-bottom:1px solid var(--heading-green)}
.welcome p{margin-top:18px;font-size:14.4px;line-height:18px;color:var(--body-text);text-align:justify;padding-left:1px}
.site-footer{position:absolute;left:0;top:690px;width:1200px;height:102px;background:linear-gradient(var(--footer-top),var(--footer-bottom));border-top:2px solid #8b97a3;color:var(--white);text-align:center}
.footer-nav{margin-top:19px;font-size:14px}
.footer-nav span{margin:0 7px}
.copyright{margin-top:14px;font-size:14px}
</style>
</head>
<body>
<header class="brand">
  <div class="brand-name"><span class="brand-dot"></span>Maple Beacon</div>
  <p class="tagline">Because You´re Awesome!</p>
</header>
<ul class="main-nav">
  <li class="current"><svg viewBox="0 0 17 12"><ellipse cx="8.5" cy="6" rx="8" ry="5" fill="var(--leaf)" transform="rotate(-20 8.5 6)"/></svg>Strategy</li>
  <li><svg viewBox="0 0 17 12"><ellipse cx="8.5" cy="6" rx="8" ry="5" fill="var(--leaf)" transform="rotate(-20 8.5 6)"/></svg>Portfolio</li>
  <li><svg viewBox="0 0 17 12"><ellipse cx="8.5" cy="6" rx="8" ry="5" fill="var(--leaf)" transform="rotate(-20 8.5 6)"/></svg>About Us</li>
  <li><svg viewBox="0 0 17 12"><ellipse cx="8.5" cy="6" rx="8" ry="5" fill="var(--leaf)" transform="rotate(-20 8.5 6)"/></svg>Contact Us</li>
  <li><svg viewBox="0 0 17 12"><ellipse cx="8.5" cy="6" rx="8" ry="5" fill="var(--leaf)" transform="rotate(-20 8.5 6)"/></svg>Blog</li>
</ul>
<section class="hero">
  <div class="hero-photo" role="img" aria-label="Close-up photograph of fresh green grass blades in soft light"></div>
  <h2 class="hero-title">MAPLE BEACON</h2>
  <div class="hero-dots"><span></span><span></span><span></span><span></span></div>
</section>
<section class="band">
  <div class="connect">Connect<br>with us !</div>
  <div class="social"><span></span><span></span><span></span><span></span><span></span></div>
  <p class="newsletter">Get Tips and Tricks! Subscribe to our Newsletter.</p>
  <a class="btn btn-subscribe">Subscribe</a>
  <a class="btn btn-quote">Get a Free Quote</a>
</section>
<main class="welcome">
  <h1>WELCOME!</h1>
  <p>Lorem ipsum dolor sit amet, consectetur adipisicing elit, sed do eiusmod tempor incididunt ut labore et dolore magna aliqua. Ut enim ad minim veniam, quis nostrud exercitation ullamco laboris nisi ut aliquip ex ea commodo consequat. Duis aute irure dolor in reprehenderit in voluptate velit esse cillum dolore eu fugiat nulla pariatur. Excepteur sint occaecat cupidatat non proident, sunt in culpa qui offi-cia deseruntilil</p>
  <p>Sed ut perspiciatis unde omnis iste natus error sit voluptatem accusantium doloremque laudantium, totam rem aperiam, eaque ipsa quae ab illo inventore veritatis et quasi architecto beatae vitae dicta sunt explicabo. Nemo enim ipsam voluptatem quia voluptas sit aspernatur aut odit aut fugit, sed quia</p>
</main>
<footer class="site-footer">
  <nav class="footer-nav">Site Map<span>|</span>Strategy<span>|</span>Portfolio<span>|</span>About Us<span>|</span>Contact Us<span>|</span>Blog</nav>
  <p class="copyright">© MAPLE BEACON INC. 2013</p>
</footer>
</body>
</html>
```